Lip Balm Label Design

Design a label for a Lavender-Mint lip balm. We make high-quality natural essential oil products. Please use the old label as an example of what exists. The label should include purple. The final design should be eye-catching and distinct. The file should be in an AI file.

Here is the information that should be included on the label:
1) ingredients:Theobroma Cacao (Cocoa) Seed Butter, Theobroma grandiflorum Ultra Refined Butter, beesewax, Calendula Officinalis Flower Oil, Prunus Amygdalus Dulcis (Sweet Almond) Oil, cetyl alcohol and Tocopherol. Lavandula Angustifolia (Lavender) Oil and Mentha Piperita (Peppermint) Oil.

2) www.kelsoroothaven.com

3) Brand name and logo: K. Elso Aromatherapy (logo is attached- you can use with form)

```html
<!DOCTYPE html>
<html lang="en">
<head>
<meta charset="utf-8">
<title>Lavender Mint Lip Balm Label</title>
<link rel="stylesheet" href="https://fonts.googleapis.com/css2?family=Caveat+Brush&family=Jost:wght@400&display=swap">
<style>
  :root {
    --backdrop: #5e4683;
    --label-white: #ffffff;
    --brand-green: #6aa832;
    --lavender-band: #b1a5d6;
    --wash-deep: #8a5fb6;
    --wash-mid: #a77fc6;
    --wash-pink: #d9a3cf;
    --wash-pale: #e7dcf0;
    --ink-light: #ffffff;
  }
  * { box-sizing: border-box; margin: 0; padding: 0; }
  html, body { width: 1200px; height: 1200px; overflow: hidden; }
  body {
    background: var(--backdrop);
    font-family: "Jost", sans-serif;
    position: relative;
  }
  .label {
    position: absolute;
    left: 207px;
    top: 100px;
    width: 786px;
    height: 1000px;
    background: var(--label-white);
    overflow: hidden;
  }
  .brand {
    position: absolute;
    left: 0;
    width: 625px;
    top: 88px;
    display: flex;
    align-items: center;
    justify-content: center;
    gap: 12px;
  }
  .brand-dot {
    width: 26px;
    height: 26px;
    border-radius: 50%;
    background: var(--brand-green);
  }
  .brand-name {
    font-size: 30px;
    color: var(--brand-green);
    font-weight: 400;
    letter-spacing: 0.02em;
  }
  .watercolor-wash {
    position: absolute;
    left: 0;
    top: 150px;
    width: 640px;
    height: 870px;
  }
  .product-name {
    position: absolute;
    left: -108px;
    top: 505px;
    width: 690px;
    height: 150px;
    transform: rotate(-90deg);
    color: var(--ink-light);
    font-family: "Caveat Brush", cursive;
    font-size: 128px;
    line-height: 150px;
    text-align: center;
    white-space: nowrap;
    font-weight: 400;
  }
  .herb-sprig {
    position: absolute;
    left: 330px;
    top: 395px;
    width: 170px;
    height: 345px;
  }
  .product-type {
    position: absolute;
    left: 318px;
    top: 778px;
    color: var(--ink-light);
    font-size: 41px;
    line-height: 46px;
    letter-spacing: 0.16em;
  }
  .net-weight {
    position: absolute;
    left: 318px;
    top: 894px;
    color: var(--ink-light);
    font-size: 18px;
    letter-spacing: 0.02em;
  }
  .website {
    position: absolute;
    left: -97px;
    top: 486px;
    width: 345px;
    height: 24px;
    transform: rotate(90deg);
    color: var(--ink-light);
    font-size: 20px;
    letter-spacing: 0.2em;
    text-align: center;
    white-space: nowrap;
  }
  .ingredients-band {
    position: absolute;
    left: 625px;
    top: 73px;
    width: 121px;
    height: 854px;
    background: var(--lavender-band);
  }
  .ingredients {
    position: absolute;
    left: 258px;
    top: 440px;
    width: 854px;
    height: 121px;
    padding: 8px 10px;
    transform: rotate(-90deg);
    color: var(--ink-light);
    font-size: 15px;
    line-height: 20.5px;
    text-transform: uppercase;
    text-align: justify;
    letter-spacing: 0.01em;
  }
</style>
</head>
<body>
  <main class="label">
    <div class="brand">
      <span class="brand-dot"></span>
      <span class="brand-name">K. Elso Aromatherapy</span>
    </div>

    <svg class="watercolor-wash" viewBox="0 0 640 870" role="img" aria-label="Soft purple and pink watercolour wash behind the product name">
      <defs>
        <radialGradient id="wash" cx="0.48" cy="0.5" r="0.55">
          <stop offset="0" stop-color="var(--wash-pink)"/>
          <stop offset="0.35" stop-color="var(--wash-mid)"/>
          <stop offset="0.6" stop-color="var(--wash-deep)"/>
          <stop offset="0.85" stop-color="var(--wash-pale)"/>
          <stop offset="1" stop-color="var(--wash-pale)" stop-opacity="0"/>
        </radialGradient>
      </defs>
      <path d="M60 170 C120 40 300 10 430 60 C560 110 640 250 620 420 C605 580 560 720 450 800 C330 880 150 860 70 760 C-10 650 0 300 60 170 Z" fill="url(#wash)"/>
    </svg>

    <svg class="herb-sprig" viewBox="0 0 170 345" role="img" aria-label="Line illustration of a lavender sprig with a mint leaf">
      <defs>
        <radialGradient id="sprigGlow" cx="0.5" cy="0.5" r="0.5">
          <stop offset="0" stop-color="#ffffff" stop-opacity="0.45"/>
          <stop offset="1" stop-color="#ffffff" stop-opacity="0"/>
        </radialGradient>
      </defs>
      <ellipse cx="85" cy="172" rx="85" ry="172" fill="url(#sprigGlow)"/>
    </svg>

    <h1 class="product-name">Lavender Mint</h1>

    <p class="website">www.kelsoroothaven.com</p>

    <p class="product-type">LIP<br>BALM</p>
    <p class="net-weight">0.15 oz (4.4 ML)</p>

    <div class="ingredients-band"></div>
    <p class="ingredients">Ingredients: Theobroma Cacao (Cocoa) Seed Butter, Theobroma Grandiflorum Ultra Refined Butter, Beesewax, Calendula Officinalis Flower Oil, Prunus Amygdalus Dulcis (Sweet Almond) Oil, Cetyl Alcohol and Tocopherol. Lavandula Angustifolia (Lavender) Oil and Mentha Piperita (Peppermint) Oil.</p>
  </main>
</body>
</html>
```